Redesign of LumoWordfind.com in Bootstrap 4

Current design of LumoWordfind.com is not responsive. We need to change it to latest version of Bootstrap 4 keeping essential elements in place.

Apart from home page, we need designs for http://www.lumowordfind.com/meaning/cat also.

Coding

Number of Pages Required

2 page

Colors
34a7d8

Requirements
Must have
• Bootstrap 4

```html
<!DOCTYPE html>
<html lang="en">
<head>
<meta charset="utf-8">
<title>Lumo Wordfind</title>
<link href="https://fonts.googleapis.com/css2?family=Roboto:wght@300;400;500;700&display=swap" rel="stylesheet">
<style>
:root{
  --orange:#fbb01f;
  --orange-deep:#f7a10b;
  --blue:#34a7d8;
  --blue-btn:#2b97d2;
  --ink:#222;
  --muted:#666;
  --light:#f1f1f1;
  --dark:#111;
  --navy:#2d3142;
}
*{margin:0;padding:0;box-sizing:border-box}
html,body{width:816px;height:1200px;overflow:hidden}
body{font-family:'Roboto',sans-serif;color:var(--ink);background:#fff;position:relative}
.abs{position:absolute}

/* hero */
.hero{left:0;top:0;width:816px;height:368px;background:linear-gradient(135deg,#fdc53a 0%,#fbb01f 45%,#f8a412 100%);overflow:hidden}
.header{left:60px;top:0;width:697px;height:82px;background:#fff;box-shadow:0 10px 14px -8px rgba(0,0,0,.35)}
.brand{left:22px;top:24px;display:flex;align-items:center;gap:8px;font-size:20px;font-weight:700;color:var(--blue)}
.brand-dot{width:20px;height:20px;background:var(--orange);border-radius:50%}
.nav{left:261px;top:37px;display:flex;gap:19px;font-size:10px;text-transform:uppercase}
.nav a{color:var(--ink);text-decoration:none}
.nav a.active{color:var(--blue)}
.login{left:638px;top:31px;width:45px;height:22px;border:1px solid var(--blue);border-radius:2px;color:var(--blue);font-size:9px;display:flex;align-items:center;justify-content:center}
.hero-title{left:0;width:816px;top:114px;text-align:center;color:#fff;font-size:21px;font-weight:500;text-shadow:0 1px 2px rgba(0,0,0,.15)}
.search-frame{left:142px;top:163px;width:532px;height:71px;background:var(--orange-deep);border:1px solid #f39a06;box-shadow:0 3px 6px rgba(0,0,0,.2)}
.search-box{left:11px;top:12px;width:510px;height:45px;background:#fff;border-radius:2px;display:flex;align-items:center;padding:0 16px;justify-content:space-between;font-size:11.5px;color:#555}
.hero-art{left:266px;top:246px;width:280px;height:122px;background:linear-gradient(180deg,rgba(255,220,90,.25),#d7c52a 60%,var(--navy) 61%)}
.slide-ctrl{left:712px;top:329px;display:flex;gap:1px}
.slide-ctrl span{width:19px;height:23px;background:#3a3018;display:flex;align-items:center;justify-content:center}

/* welcome */
.welcome{left:0;top:368px;width:816px;height:348px;background:var(--light)}
.welcome h2{position:absolute;top:30px;width:816px;text-align:center;font-size:15.5px;font-weight:400}
.welcome h2 span{color:var(--blue)}
.intro{position:absolute;left:86px;top:59px;width:644px;text-align:center;font-size:8.5px;line-height:14.4px;color:var(--muted)}
.feature{position:absolute;top:124px;width:140px;text-align:center}
.feature .ring{width:74px;height:74px;border-radius:50%;background:#fff;margin:0 auto;border:3px solid #f5f5f5;box-shadow:0 2px 5px rgba(0,0,0,.18);display:flex;align-items:center;justify-content:center}
.feature h3{font-size:9.5px;font-weight:500;margin-top:18px;text-transform:uppercase}
.feature p{font-size:7.4px;line-height:12px;color:var(--muted);margin-top:7px}
.btn{display:inline-block;margin-top:14px;background:var(--blue-btn);color:#fff;font-size:7.2px;padding:6px 12px;border-radius:2px;text-transform:uppercase;box-shadow:0 1px 2px rgba(0,0,0,.25)}
.side-arrow{position:absolute;top:198px}

/* promo */
.promo{left:60px;top:736px;width:533px;height:195px;background:linear-gradient(90deg,#e4e4e4,#f6f6f6);border:1px solid #ddd}
.monitor{left:14px;top:23px;width:193px;height:130px;background:#1c1c1c;border-radius:4px;padding:7px}
.screen{width:100%;height:100%;background:linear-gradient(135deg,#fafafa,#e3e3e3);display:flex;align-items:center;justify-content:center;gap:6px;font-weight:700;font-size:15px;color:var(--blue)}
.stand{left:94px;top:153px;width:36px;height:26px;background:linear-gradient(#ccc,#f1f1f1);clip-path:polygon(20% 0,80% 0,100% 100%,0 100%)}
.promo h4{position:absolute;left:218px;top:26px;color:var(--blue);font-size:12px;font-weight:400;text-transform:uppercase}
.ticks{position:absolute;left:218px;top:49px;list-style:none;font-size:9.5px;color:#333}
.ticks li{display:flex;align-items:center;gap:7px;height:21px}
.poster{left:601px;top:736px;width:155px;height:195px;background:linear-gradient(180deg,#2a2e3a 0%,#3e4250 70%,#c65a32 85%,#2a2e3a 100%);border:1px solid #ccc}

/* browse */
.browse{left:61px;top:961px;display:flex;align-items:center;gap:6px;font-size:8.5px;color:var(--blue)}
.letters{display:flex;gap:3px;background:#eef3f8;padding:3px}
.letters span{width:14px;height:14px;border:1px solid #7aa7c6;font-size:7px;color:#333;display:flex;align-items:center;justify-content:center;background:#fff}

/* footer */
.footer{left:0;top:1002px;width:816px;height:150px;background:var(--blue);color:#fff}
.footer h5{position:absolute;top:26px;font-size:10.5px;font-weight:400;text-transform:uppercase}
.links{position:absolute;left:68px;top:52px;list-style:none;font-size:7.5px;line-height:16.8px}
.links li::before{content:"\25B8";margin-right:4px;font-size:6px}
.fcopy{position:absolute;font-size:7.5px;line-height:12px}
.view{position:absolute;left:207px;top:95px;width:47px;height:18px;background:#f4f4f4;color:#333;font-size:8px;display:flex;align-items:center;justify-content:center;border-radius:2px}
.subscribe{position:absolute;left:611px;top:89px;display:flex;height:22px}
.subscribe .field{width:100px;background:#fff;color:#555;font-size:7.5px;display:flex;align-items:center;padding-left:9px}
.subscribe .go{width:39px;background:var(--dark);font-size:8px;display:flex;align-items:center;justify-content:center}
.social{position:absolute;left:611px;top:122px;display:flex;gap:10px}
.social span{width:24px;height:24px;border:1px solid rgba(255,255,255,.8);border-radius:50%;display:flex;align-items:center;justify-content:center}
.social span i{width:7px;height:7px;background:#fff;border-radius:1px}
.bottom{left:0;top:1152px;width:816px;height:48px;background:var(--dark);color:#fff;font-size:7.5px;display:flex;align-items:center;justify-content:center}
</style>
</head>
<body>

<section class="hero abs">
  <div class="hero-art abs" role="img" aria-label="Open book with letters flying out"></div>
  <header class="header abs">
    <div class="brand abs"><span class="brand-dot"></span>Lumo Wordfind</div>
    <nav class="nav abs">
      <a class="active">Home</a><a>Idioms</a><a>Common Errors</a><a>Crossword</a><a>Blog</a><a>Contact</a>
    </nav>
    <div class="login abs">LOGIN</div>
  </header>
  <h1 class="hero-title abs">LUMO ENGLISH DICTIONARY</h1>
  <div class="search-frame abs">
    <div class="search-box abs">
      <span>Enter a word or phrase</span>
      <svg width="14" height="14" viewBox="0 0 14 14"><circle cx="5.8" cy="5.8" r="4.3" fill="none" stroke="#444" stroke-width="1.8"/><line x1="9" y1="9" x2="13" y2="13" stroke="#444" stroke-width="2"/></svg>
    </div>
  </div>
  <div class="slide-ctrl abs">
    <span><svg width="8" height="12"><polyline points="7,1 1,6 7,11" fill="none" stroke="#fff" stroke-width="1"/></svg></span>
    <span><svg width="8" height="12"><polyline points="1,1 7,6 1,11" fill="none" stroke="#fff" stroke-width="1"/></svg></span>
  </div>
</section>

<section class="welcome abs">
  <h2>WELCOME TO <span>LUMO WORDFIND</span></h2>
  <p class="intro">Lorem Ipsum has been the industry's standard dummy text ever since the 1500s, when an unknown printer took a galley of type and scrambled it to make a type specimen book. It has survived not only five centuries, but also the leap into electronic typesetting, remaining essentially unchanged. It was popularised in the 1960s with the release of Letraset sheets containing Lorem Ipsum passages, and more recently with desktop publishing software</p>

  <svg class="side-arrow" style="left:31px" width="12" height="18"><polyline points="10,1 2,9 10,17" fill="none" stroke="#777" stroke-width="2"/></svg>
  <svg class="side-arrow" style="left:760px" width="12" height="18"><polyline points="2,1 10,9 2,17" fill="none" stroke="#777" stroke-width="2"/></svg>

  <div class="feature" style="left:63px">
    <div class="ring"><svg width="22" height="16"><rect x="3" y="1" width="16" height="11" fill="none" stroke="#f7a10b" stroke-width="1.6"/><rect x="0" y="13" width="22" height="2" fill="#f7a10b"/></svg></div>
    <h3>English Tidbit</h3>
    <p>Lorem Ipsum has been the industry's standard dummy text ever since the 1500s, when an unknown printer</p>
    <span class="btn">Read More</span>
  </div>
  <div class="feature" style="left:246px">
    <div class="ring"><svg width="20" height="20" viewBox="0 0 20 20"><circle cx="10" cy="10" r="6.5" fill="none" stroke="#f7a10b" stroke-width="4" stroke-dasharray="3 2"/><circle cx="10" cy="10" r="4.5" fill="#f7a10b"/><circle cx="10" cy="10" r="2" fill="#fff"/></svg></div>
    <h3>Daily Crossword</h3>
    <p>Lorem Ipsum has been the industry's standard dummy text ever since the 1500s, when an unknown printer</p>
    <span class="btn">Solve Now</span>
  </div>
  <div class="feature" style="left:428px">
    <div class="ring"><svg width="26" height="20"><circle cx="7" cy="5" r="3.5" fill="#f7a10b"/><circle cx="19" cy="5" r="3.5" fill="#f7a10b"/><circle cx="13" cy="8" r="4" fill="#f7a10b"/><path d="M1 16c0-5 12-5 12 0zM13 16c0-5 12-5 12 0zM6 20c0-6 14-6 14 0z" fill="#f7a10b"/></svg></div>
    <h3>Flarefox Addon</h3>
    <p>Lorem Ipsum has been the industry's standard dummy text ever since the 1500s, when an unknown printer</p>
    <span class="btn">Get It Now</span>
  </div>
  <div class="feature" style="left:611px">
    <div class="ring"><svg width="22" height="22"><polygon points="1,10 21,1 14,21 10,13" fill="#f7a10b"/></svg></div>
    <h3>Designed for Pomo Phone</h3>
    <p>Lorem Ipsum has been the industry's standard dummy text ever since the 1500s, when an unknown printer</p>
    <span class="btn">Read More</span>
  </div>
</section>

<section class="promo abs">
  <div class="monitor abs"><div class="screen"><span class="brand-dot"></span>Lumo Wordfind</div></div>
  <div class="stand abs"></div>
  <h4>Search, Save and Master Words</h4>
  <ul class="ticks">
    <li><svg width="9" height="8"><polyline points="1,4 3.5,7 8,1" fill="none" stroke="#f7a10b" stroke-width="2"/></svg>Search from more than 300,000 words and phrases</li>
    <li><svg width="9" height="8"><polyline points="1,4 3.5,7 8,1" fill="none" stroke="#f7a10b" stroke-width="2"/></svg>Multiple usages to clarify the context</li>
    <li><svg width="9" height="8"><polyline points="1,4 3.5,7 8,1" fill="none" stroke="#f7a10b" stroke-width="2"/></svg>Audio, phonetics, meanings, synonyms and antonyms</li>
    <li><svg width="9" height="8"><polyline points="1,4 3.5,7 8,1" fill="none" stroke="#f7a10b" stroke-width="2"/></svg>Save the words to your personal deck and access from anywhere</li>
    <li><svg width="9" height="8"><polyline points="1,4 3.5,7 8,1" fill="none" stroke="#f7a10b" stroke-width="2"/></svg>It's FREE</li>
  </ul>
</section>
<div class="poster abs" role="img" aria-label="Education charity poster: child reading beside a stack of books on a chalkboard background"></div>

<div class="browse abs">
  <span>Browse Dictionary</span>
  <div class="letters">
    <span>A</span><span>B</span><span>C</span><span>D</span><span>E</span><span>F</span><span>G</span><span>H</span><span>I</span><span>J</span><span>K</span><span>L</span><span>M</span><span>N</span><span>O</span><span>P</span><span>Q</span><span>R</span><span>S</span><span>T</span><span>U</span><span>V</span><span>W</span><span>X</span><span>Y</span><span>Z</span>
  </div>
</div>

<footer class="footer abs">
  <h5 style="left:68px">Links</h5>
  <ul class="links"><li>Home</li><li>About Us</li><li>Past Performance</li><li>Pricing</li><li>Contact</li></ul>
  <h5 style="left:208px">Crossword</h5>
  <p class="fcopy" style="left:208px;top:53px;width:172px;text-align:justify">Lorem Ipsum has been the industry's standard dummy text ever since the 1500s, when an unknown printer took a galley</p>
  <div class="view">View</div>
  <h5 style="left:437px">Get in Touch</h5>
  <p class="fcopy" style="left:438px;top:53px">Address : 48 Linden Row,<br>Harborview, NJ</p>
  <p class="fcopy" style="left:438px;top:90px">Phone : 555 318 2740</p>
  <p class="fcopy" style="left:438px;top:113px">Email : hello@lumowordfind.com</p>
  <h5 style="left:611px">Newsletter</h5>
  <p class="fcopy" style="left:611px;top:52px;width:140px">Your about us information would fit here nicely.</p>
  <div class="subscribe"><span class="field">Email address</span><span class="go">Submit</span></div>
  <div class="social"><span><i></i></span><span><i></i></span><span><i></i></span></div>
</footer>
<div class="bottom abs">Copyright © 2016. All Rights Reserved</div>

</body>
</html>
```